Australian Trucking Company Requires Professional Looking Stationary

We require a professional looking stationary design that incorporates our newly designed logo.

Our business, called "Brell Haulage Contracting", provides contracting work, transport and logistics to business in Western Australia particularly with links to the mining sector.

We are a small business looking to expand and our new logo and our new stationary will help develop our brand image in our market place.

Target Market(s)

Businesses and Corporation with links to the Mining Sector

Industry/Entity Type

Small Business

Requirements
Must have
• The letterhead must have the following details:
The new logo

Text saying: "Brell Holdings Pty Ltd (ACN 582 316 907) ATF The Brell Discretionary Trust T/AS"
"ABN 71 834 209 553"
Address "P.O Box 817 Wattlegrove WA, 6958"
Phone: 08 9352 7140
Email: brellhaul@mailbox-example.com.au

The text on the letterhead should be editable as the details are likely to change in the near future. Provision should be made for a website address all though one isn't available at the moment.

The styling, layout and font text is entirely up to the designer.

```html
<!DOCTYPE html>
<html lang="en">
<head>
<meta charset="utf-8">
<title>Brell Haulage Contracting – Business Cards</title>
<link rel="stylesheet" href="https://fonts.googleapis.com/css2?family=Oswald:wght@700&family=PT+Sans:wght@400;700&display=swap">
<style>
  :root {
    --bg: #ecebe8;
    --card: #ffffff;
    --red: #e8202a;
    --brand-red: #8e1b1b;
    --ink: #1a1a1a;
    --white: #ffffff;
  }
  * { margin: 0; padding: 0; box-sizing: border-box; }
  html, body { width: 1200px; height: 426px; overflow: hidden; }
  body {
    background: var(--bg);
    font-family: "PT Sans", Arial, sans-serif;
    color: var(--ink);
    position: relative;
  }
  .card {
    position: absolute;
    width: 518px;
    height: 294px;
    background: var(--card);
    border-radius: 22px;
    overflow: hidden;
    box-shadow: 0 2px 6px rgba(0,0,0,0.18);
  }
  .card--front { left: 50px; top: 68px; }
  .card--back { left: 602px; top: 66px; }

  .rule {
    position: absolute; left: 0; right: 0;
    height: 2px; background: var(--red);
  }
  .band {
    position: absolute; left: 0; right: 0;
    background: var(--red);
  }
  .card--front .rule--top { top: 148px; }
  .card--front .band { top: 156px; height: 66px; }
  .card--front .rule--bottom { top: 228px; }
  .card--back .rule--top { top: 146px; }
  .card--back .band { top: 156px; height: 66px; }
  .card--back .rule--bottom { top: 230px; }

  .art { position: absolute; }
  .art--logo-truck {
    left: 26px; top: 36px; width: 108px; height: 88px;
    background: linear-gradient(135deg, #b5b5b5, #555555);
    border-radius: 6px;
  }
  .art--band-truck {
    left: 196px; top: 164px; width: 56px; height: 42px;
    background: linear-gradient(135deg, #3a3a3a, #111111);
    border-radius: 4px;
  }
  .art--hero-truck {
    left: 198px; top: 40px; width: 142px; height: 190px;
    background: linear-gradient(135deg, #2e2e2e, #0a0a0a);
    border-radius: 12px;
  }

  .brand-name {
    position: absolute; left: 154px; top: 42px;
    font-family: "Oswald", "Arial Narrow", sans-serif;
    font-weight: 700;
    font-size: 25px;
    line-height: 28px;
    letter-spacing: 1.5px;
    color: var(--brand-red);
    text-transform: uppercase;
  }

  .holder {
    position: absolute; left: 26px; top: 164px;
    color: var(--white);
    text-align: center;
  }
  .holder__name { font-size: 20px; font-weight: 700; line-height: 26px; }
  .holder__role { font-size: 12px; line-height: 16px; }

  .contact {
    position: absolute; left: 266px; top: 159px;
    color: var(--white);
    font-size: 11.5px; line-height: 15px;
  }
  .contact__row { display: flex; align-items: center; gap: 4px; white-space: nowrap; }
  .contact svg { width: 10px; height: 10px; flex: none; }

  .legal {
    position: absolute; left: 0; right: 0; top: 238px;
    text-align: center;
    font-size: 11px; line-height: 16.5px;
  }

  .web {
    position: absolute; left: 58px; top: 182px;
    color: var(--white); font-size: 12px;
  }
</style>
</head>
<body>

<section class="card card--front">
  <div class="art art--logo-truck" role="img" aria-label="Grey truck illustration beside the company name"></div>
  <div class="brand-name">Brell<br>Haulage<br>Contracting</div>

  <div class="rule rule--top"></div>
  <div class="band"></div>
  <div class="rule rule--bottom"></div>

  <div class="holder">
    <div class="holder__name">Persons name</div>
    <div class="holder__role">Manager</div>
  </div>

  <div class="art art--band-truck" role="img" aria-label="Small black truck illustration"></div>

  <div class="contact">
    <div class="contact__row">
      <svg viewBox="0 0 10 10"><path d="M2 1 L4 3 L3 4 Q4 6 6 7 L7 6 L9 8 L8 9 Q3 9 1 2 Z" fill="#fff"/></svg>
      08 9352 7140
    </div>
    <div class="contact__row">
      <svg viewBox="0 0 10 10"><rect x="0.5" y="2" width="9" height="6" fill="none" stroke="#fff"/><path d="M0.5 2 L5 5.5 L9.5 2" fill="none" stroke="#fff"/></svg>
      brellhaul@mailbox-example.com.au
    </div>
    <div class="contact__row">
      <svg viewBox="0 0 10 10"><path d="M5 1 L9.5 5 H8 V9 H2 V5 H0.5 Z" fill="#fff"/></svg>
      P.O Box 817 Wattlegrove WA, 6958
    </div>
    <div class="contact__row">
      <svg viewBox="0 0 10 10"><circle cx="5" cy="5" r="4.2" fill="none" stroke="#fff"/><ellipse cx="5" cy="5" rx="1.8" ry="4.2" fill="none" stroke="#fff"/><path d="M1 5 H9" stroke="#fff"/></svg>
      www.brellhaulsite.com
    </div>
  </div>

  <div class="legal">
    Brell Holdings Pty Ltd (ACN 582 316 907)<br>
    ATF&nbsp; The Brell Discretionary Trust T/AS<br>
    ABN 71 834 209 553
  </div>
</section>

<section class="card card--back">
  <div class="rule rule--top"></div>
  <div class="band"></div>
  <div class="rule rule--bottom"></div>
  <div class="web">www.brellhaulsite.com</div>
  <div class="art art--hero-truck" role="img" aria-label="Large black truck illustration, front three-quarter view"></div>
</section>

</body>
</html>
```